American cannabis tech company business card design

Pavrel.com is seeking a modern, professional, and brand-aligned business card that represents our company and its core values: Mission, Story, Values, and Impact. As an innovative cannabis company, we want a business card that is not only visually appealing but also serves as a representation of who we are and what we stand for.

Project Scope: Design a double-sided business card that integrates our brand identity and core values. Incorporate our key brand elements, ensuring a sleek and contemporary aesthetic. Visually reflect our core values (Mission, Story, Values, Impact) in a way that is engaging yet professional.

Target Market(s)

Vendors, third parties,

Contact Information for Business Card

Contact details (name, title, email, phone, website, etc.)

Font styles to use
Other font styles liked:
• Caslon, Centra

Colors

Designer to choose colors to be used in the design.

Requirements
Must have
• Pavrel.com logo and branding A creative yet clean way to integrate our core values (Mission, Story, Values, Impact) Modern typography and a well-structured layout
Nice to have
• forest green, grey, white, black
Should not have
• references to marijuana, leafs, plants, or related product

```html
<!DOCTYPE html>
<html lang="en">
<head>
<meta charset="utf-8">
<title>Pavrel.com Business Card</title>
<link href="https://fonts.googleapis.com/css2?family=Libre+Caslon+Text:wght@400;700&family=Montserrat:wght@400;500&display=swap" rel="stylesheet">
<style>
  :root {
    --stage: #232323;
    --forest: #1c3520;
    --forest-deep: #12251a;
    --forest-panel: #263d29;
    --paper: #ffffff;
    --cream: #f7f4ec;
    --ink-green: #1f3a22;
    --ink: #1d1d1d;
  }
  * { box-sizing: border-box; margin: 0; padding: 0; }
  html, body {
    width: 1200px; height: 1015px; overflow: hidden;
    background: var(--stage);
  }
  .sheet {
    width: 1200px; height: 1015px;
    display: flex; flex-direction: column; align-items: center; justify-content: center;
    gap: 56px;
  }
  .card {
    width: 700px; height: 400px;
    position: relative; overflow: hidden;
    box-shadow: 0 12px 30px rgba(0,0,0,.45);
  }

  /* Front */
  .card--front {
    background: var(--forest);
    display: flex; align-items: center; justify-content: center;
  }
  .front-wordmark {
    font-family: "Libre Caslon Text", serif;
    font-weight: 700;
    font-size: 150px;
    letter-spacing: -2px;
    color: var(--forest-deep);
  }

  /* Back */
  .card--back { display: flex; }
  .details {
    width: 46%; height: 100%;
    background: var(--paper);
    padding: 48px 0 40px 44px;
    display: flex; flex-direction: column; justify-content: space-between;
  }
  .holder-name {
    font-family: "Libre Caslon Text", serif;
    font-weight: 700; font-size: 25px;
    color: var(--ink-green);
  }
  .holder-role {
    font-family: "Libre Caslon Text", serif;
    font-weight: 700; font-size: 12px;
    color: var(--ink);
    margin: 4px 0 0 18px;
  }
  .contact { font-family: "Montserrat", sans-serif; color: var(--ink); }
  .address { font-size: 16px; line-height: 1.2; margin: 0 0 22px 48px; }
  .contact-list { list-style: none; }
  .contact-list li {
    display: flex; align-items: center; gap: 10px;
    font-size: 16px; line-height: 1.55;
    margin-left: 48px;
  }
  .contact-list svg { width: 14px; height: 14px; flex: none; }
  .brand-panel {
    flex: 1; background: var(--forest-panel);
    display: flex; align-items: center; justify-content: center;
  }
  .brand-wordmark {
    font-family: "Libre Caslon Text", serif;
    font-weight: 700; font-size: 86px;
    color: var(--cream);
  }
</style>
</head>
<body>
<main class="sheet">
  <section class="card card--front" aria-label="Card front">
    <span class="front-wordmark">Pavrel</span>
  </section>

  <section class="card card--back" aria-label="Card back">
    <div class="details">
      <div class="holder">
        <p class="holder-name">Dana Whitlow</p>
        <p class="holder-role">Owner</p>
      </div>
      <div class="contact">
        <p class="address">418 Orchard Lane, #112<br>Fairbrook, OH 43210</p>
        <ul class="contact-list">
          <li>
            <svg viewBox="0 0 16 16" aria-hidden="true"><circle cx="8" cy="8" r="8" fill="var(--ink-green)"/><path d="M5.5 4.5l1.5 1.5-0.8 1.2c.6 1.2 1.4 2 2.6 2.6l1.2-.8 1.5 1.5-1 1.2c-2.8-.4-5.4-3-5.8-5.8z" fill="#fff"/></svg>
            555-014-2297
          </li>
          <li>
            <svg viewBox="0 0 16 16" aria-hidden="true"><rect x="1" y="3" width="14" height="10" rx="1" fill="var(--ink-green)"/><path d="M1.5 3.8L8 9l6.5-5.2" stroke="#fff" stroke-width="1.2" fill="none"/></svg>
            info@pavrel.com
          </li>
          <li>
            <svg viewBox="0 0 16 16" aria-hidden="true"><circle cx="8" cy="8" r="7" fill="var(--ink-green)"/><path d="M1 8h14M8 1c-2.5 2-2.5 12 0 14M8 1c2.5 2 2.5 12 0 14" stroke="#fff" stroke-width="1" fill="none"/></svg>
            www.pavrel.com
          </li>
        </ul>
      </div>
    </div>
    <div class="brand-panel">
      <span class="brand-wordmark">Pavrel</span>
    </div>
  </section>
</main>
</body>
</html>
```